Modern card design needed for building development company

We are looking for a sharp modern new look for our business cards.
We are a New Zealand based company called TKR Ventures NZ LTD that specialises in subdividing large sections, housing and commercial buildings.
We have attached a photo of the current logo and would like to see it improved somehow as it looks a bit dated.
We are open to any colours.

Target Market(s)

Investors, Property buyers

Industry/Entity Type

Investment

Contact Information for Business Card

TKR VENTURES NZ LTD
www.tkrventuresnz.co.nz

Damon Whitcombe
Phone +64 21 938 104
Email dpwhitcombe@korumail.co.nz

Font styles to use
Serif
Sans Serif

Colors
0792cd
33a6d7
85cae6
6b449b
886aae
f04a50
ec1f27
f37122
f68d4d

Requirements
Must have
• Please try and make the logo more modern or if you have a similar one we would like to see it.

```html
<!DOCTYPE html>
<html lang="en">
<head>
<meta charset="UTF-8">
<title>TKR Ventures NZ LTD — Business Card</title>
<link href="https://fonts.googleapis.com/css2?family=Archivo:wght@600&family=Work+Sans:wght@400;500&display=swap" rel="stylesheet">
<style>
  :root {
    --page: #e6e6e8;
    --card-white: #ffffff;
    --brand-red: #9a1b2b;
    --ink-white: #ffffff;
    --shadow: rgba(0, 0, 0, 0.18);
  }
  * { box-sizing: border-box; margin: 0; padding: 0; }
  html, body {
    width: 1200px;
    height: 900px;
    overflow: hidden;
    background: var(--page);
  }
  .canvas {
    position: relative;
    width: 1200px;
    height: 900px;
  }
  .card {
    position: absolute;
    left: 250px;
    width: 700px;
    height: 400px;
    border-radius: 18px;
    overflow: hidden;
    box-shadow: 0 10px 30px var(--shadow);
  }
  .card-front { top: 30px; background: var(--card-white); }
  .card-back  { top: 470px; background: var(--brand-red); }

  .wordmark {
    position: absolute;
    display: flex;
    flex-direction: column;
    align-items: center;
    gap: 14px;
    font-family: "Work Sans", sans-serif;
    font-weight: 500;
    letter-spacing: 0.08em;
    text-align: center;
  }
  .wordmark-mark {
    width: 46px;
    height: 46px;
    border: 3px solid currentColor;
  }
  .wordmark-name { font-size: 24px; line-height: 1.3; }

  .card-front .wordmark {
    left: 0; right: 0; top: 128px;
    color: var(--brand-red);
  }
  .card-back .wordmark {
    left: 40px; width: 250px; top: 118px;
    color: var(--ink-white);
  }
  .card-back .wordmark-name { font-size: 20px; }

  .divider {
    position: absolute;
    left: 318px;
    top: 100px;
    width: 2px;
    height: 190px;
    background: var(--ink-white);
  }
  .contact {
    position: absolute;
    left: 356px;
    top: 122px;
    color: var(--ink-white);
  }
  .contact-name {
    font-family: "Archivo", sans-serif;
    font-weight: 600;
    font-size: 29px;
    letter-spacing: 0.01em;
    margin-bottom: 16px;
  }
  .contact-line {
    display: flex;
    align-items: center;
    gap: 12px;
    font-family: "Work Sans", sans-serif;
    font-size: 18px;
    line-height: 1.45;
  }
  .contact-icon { width: 14px; height: 14px; flex: none; }

  .web-band {
    position: absolute;
    left: 0; bottom: 0;
    width: 700px;
    height: 70px;
  }
  .web-address {
    position: absolute;
    right: 30px;
    bottom: 20px;
    font-family: "Work Sans", sans-serif;
    font-size: 19px;
    color: var(--brand-red);
  }
  .web-address strong { font-weight: 500; }
</style>
</head>
<body>
<main class="canvas">

  <section class="card card-front" aria-label="Card front">
    <div class="wordmark">
      <span class="wordmark-mark"></span>
      <span class="wordmark-name">TKR VENTURES NZ LTD</span>
    </div>
  </section>

  <section class="card card-back" aria-label="Card back">
    <div class="wordmark">
      <span class="wordmark-mark"></span>
      <span class="wordmark-name">TKR VENTURES NZ LTD</span>
    </div>

    <div class="divider"></div>

    <div class="contact">
      <p class="contact-name">DAMON WHITCOMBE</p>
      <p class="contact-line">
        <svg class="contact-icon" viewBox="0 0 24 24" fill="none" stroke="currentColor" stroke-width="2.2" stroke-linecap="round" stroke-linejoin="round">
          <path d="M6 3h3l2 5-2.5 1.5a11 11 0 0 0 6 6L16 13l5 2v3a2 2 0 0 1-2 2A16 16 0 0 1 4 5a2 2 0 0 1 2-2z"/>
        </svg>
        +64 21 938 104
      </p>
      <p class="contact-line">
        <svg class="contact-icon" viewBox="0 0 24 24" fill="none" stroke="currentColor" stroke-width="2.2" stroke-linejoin="round">
          <rect x="3" y="5" width="18" height="14" rx="1"/>
          <path d="M3 6l9 7 9-7"/>
        </svg>
        dpwhitcombe@korumail.co.nz
      </p>
    </div>

    <svg class="web-band" viewBox="0 0 700 70" preserveAspectRatio="none" aria-hidden="true">
      <polygon points="390,0 700,0 700,70 320,70" fill="var(--card-white)"/>
    </svg>
    <p class="web-address">www.<strong>tkrventuresnz.co.nz</strong>.com</p>
  </section>

</main>
</body>
</html>
```